LM-Steuerberatung WordPress Site fully implemented (tax advisor)

Hello!
I need a little Wordpress Site for my newly founded Tax-Advisor Company.
I am a one-man Office advising in the area of Crypto-Currency.
PLEASE only provide a Design, if you can also Implement a WP-Site afterwards on an existing Webspace.

Please find the Content and Website-Description in the attached Document

Language for the Website is German (for now)

Target Market(s)

Tax-Advisory (specialized in Crypto Currency)

Coding

Coded - Design and coding required

Number of Pages Required

5+ page

Font styles to use
Sans Serif

Requirements
Must have
• Wordpress Implementation afterwards - Details according to attached Project Information Document

```html
<!DOCTYPE html>
<html lang="de">
<head>
<meta charset="utf-8">
<title>LM-Steuerberatung</title>
<link href="https://fonts.googleapis.com/css2?family=Libre+Franklin:wght@400;500&family=Poppins:wght@400&family=Montserrat:wght@700&family=Hind:wght@400;500;600&display=swap" rel="stylesheet">
<style>
:root{
  --navy:#1b2a42;
  --ink:#2a2a2a;
  --muted:#5a5a5a;
  --white:#ffffff;
  --footer-muted:#b9c0cc;
  --wave-1:#d4d4d4;
  --wave-2:#f2f2f2;
}
*{margin:0;padding:0;box-sizing:border-box}
html,body{width:1069px;height:1200px;overflow:hidden;background:var(--white)}
body{position:relative;font-family:"Libre Franklin",Arial,sans-serif;color:var(--ink)}
.abs{position:absolute}

.hero-art{left:0;top:0;width:1069px;height:640px;
  background:
    radial-gradient(ellipse 260px 360px at 1000px 260px,var(--wave-1),transparent 70%),
    radial-gradient(ellipse 420px 120px at 520px 520px,var(--wave-1),transparent 70%),
    radial-gradient(ellipse 140px 260px at 20px 180px,var(--wave-2),transparent 75%),
    radial-gradient(ellipse 300px 80px at 150px 570px,var(--wave-2),transparent 75%),
    linear-gradient(180deg,var(--white),var(--white));}

.brand{left:99px;top:31px;display:flex;align-items:center;gap:9px}
.brand-mark{width:26px;height:26px;background:var(--navy)}
.brand-name{font-family:"Montserrat",sans-serif;font-weight:700;font-size:17px;letter-spacing:.3px;color:var(--navy)}

.main-nav{left:398px;top:35px;display:flex;gap:25px;font-size:13px;color:var(--navy)}
.main-nav a{color:inherit;text-decoration:none;position:relative}
.main-nav a.active::after{content:"";position:absolute;left:0;right:0;bottom:-7px;height:2px;background:var(--navy)}
.cta{left:796px;top:24px;width:180px;height:38px;background:var(--navy);color:var(--white);border-radius:3px;
  font-size:13px;display:flex;align-items:center;justify-content:center}

.hero-title{left:0;width:1069px;top:193px;text-align:center;font-size:37px;font-weight:500;color:var(--navy)}
.hero-sub{left:0;width:1069px;top:258px;text-align:center;font-size:12.5px;line-height:23px;color:var(--muted)}
.hero-btn{left:433px;top:326px;width:204px;height:39px;background:var(--navy);color:var(--white);border-radius:3px;
  font-size:12.5px;font-weight:500;display:flex;align-items:center;justify-content:center}

.quote{left:0;width:1069px;top:680px;text-align:center;font-family:"Poppins",sans-serif;font-size:28.5px;line-height:40px;color:var(--ink)}
.quote-initial{left:310px;top:660px;font-family:"Poppins",sans-serif;font-size:72px;color:#efefef;line-height:1;font-weight:400}

.site-footer{left:0;top:876px;width:1069px;height:324px;background:var(--navy);color:var(--white);font-family:"Hind",sans-serif}
.footer-brand{left:99px;top:57px;display:flex;align-items:center;gap:8px}
.footer-brand .brand-mark{background:var(--white);width:24px;height:24px}
.footer-brand .brand-name{color:var(--white);font-size:14.5px}
.footer-about{left:99px;top:114px;width:220px;font-size:12.5px;line-height:23px}
.col-title{font-size:18px;font-weight:600;margin-bottom:10px}
.col{top:63px}
.col ul{list-style:none}
.col li{display:flex;align-items:flex-start;gap:14px;font-size:12.5px;line-height:23px}
.col svg{flex:none;margin-top:5px}
.label{color:var(--footer-muted)}
.dot{width:9px;height:9px;border-radius:50%;background:var(--footer-muted);flex:none;margin-top:6px}
.copyright{left:0;width:1069px;top:275px;text-align:center;font-family:"Libre Franklin",sans-serif;font-size:12px}
</style>
</head>
<body>
<div class="abs hero-art" role="img" aria-label="Fließende graue Linienwellen als Hintergrunddekoration"></div>

<header>
  <div class="abs brand"><span class="brand-mark"></span><span class="brand-name">LM STEUERBERATUNG</span></div>
  <nav class="abs main-nav">
    <a class="active">Heim</a><a>Leistungen</a><a>Über mich</a><a>Kontakt</a><a>Impressum</a>
  </nav>
  <div class="abs cta">EINEN TERMIN MACHEN</div>
</header>

<section>
  <h1 class="abs hero-title">Willkommen bei LM-Steuerberatung!</h1>
  <p class="abs hero-sub">Ihrem Spezialisten bei allen steuerlichen Themen rund um Einkünfte<br>&amp; Vermögen aus Krypto-Assets.</p>
  <div class="abs hero-btn">Weiter zu unseren Leistungen</div>
</section>

<section>
  <div class="abs quote-initial">D</div>
  <p class="abs quote">Dann mach ich eine Schweizer<br>Holding-Gesellschaft– dort zahlt man<br>fast keine Steuern</p>
</section>

<footer class="abs site-footer">
  <div class="abs footer-brand"><span class="brand-mark"></span><span class="brand-name">LM STEUERBERATUNG</span></div>
  <p class="abs footer-about">Mag. Lukas Mahrer Ich blicke auf eine sehr umfassende Ausbildung und langjährige Berufserfahrung in der IT Branche zurück.</p>

  <div class="abs col" style="left:385px">
    <div class="col-title">Schnelle Links</div>
    <ul>
      <li><svg width="6" height="10" viewBox="0 0 6 10"><path d="M1 1l4 4-4 4" fill="none" stroke="#b9c0cc" stroke-width="1.2"/></svg>Home</li>
      <li><svg width="6" height="10" viewBox="0 0 6 10"><path d="M1 1l4 4-4 4" fill="none" stroke="#b9c0cc" stroke-width="1.2"/></svg>Leistungen</li>
      <li><svg width="6" height="10" viewBox="0 0 6 10"><path d="M1 1l4 4-4 4" fill="none" stroke="#b9c0cc" stroke-width="1.2"/></svg>Über mich</li>
      <li><svg width="6" height="10" viewBox="0 0 6 10"><path d="M1 1l4 4-4 4" fill="none" stroke="#b9c0cc" stroke-width="1.2"/></svg>Kontakt</li>
      <li><svg width="6" height="10" viewBox="0 0 6 10"><path d="M1 1l4 4-4 4" fill="none" stroke="#b9c0cc" stroke-width="1.2"/></svg>Impressum</li>
    </ul>
  </div>

  <div class="abs col" style="left:599px">
    <div class="col-title">Kontaktiere uns</div>
    <ul>
      <li><svg width="13" height="12" viewBox="0 0 13 12"><path d="M5 0a4 4 0 0 1 4 4c0 3-4 8-4 8S1 7 1 4a4 4 0 0 1 4-4z" fill="#b9c0cc"/><circle cx="5" cy="4" r="1.5" fill="#1b2a42"/></svg><span>Lorem ipsum dolor sit<br>amet, consectetur</span></li>
      <li><svg width="13" height="12" viewBox="0 0 13 12"><path d="M2 0l3 3-1.5 1.5a8 8 0 0 0 4 4L9 7l3 3-2 2C5 12 0 7 0 2z" fill="#b9c0cc"/></svg><span><span class="label">Telefon :</span><br>+43 512 000 417</span></li>
      <li><svg width="13" height="12" viewBox="0 0 13 12"><rect x="0" y="1" width="13" height="10" rx="1" fill="#b9c0cc"/><path d="M0 2l6.5 5L13 2" fill="none" stroke="#1b2a42" stroke-width="1.2"/></svg><span><span class="label">Email :</span><br>office@lm-steuer.example</span></li>
    </ul>
  </div>

  <div class="abs col" style="left:882px">
    <div class="col-title">Folge uns</div>
    <ul>
      <li><span class="dot"></span>Feedwerk</li>
      <li><span class="dot"></span>Kurzpost</li>
      <li><span class="dot"></span>Bilderwand</li>
      <li><span class="dot"></span>Videokanal</li>
      <li><span class="dot"></span>Berufsnetz</li>
    </ul>
  </div>

  <p class="abs copyright">© Urheberrechte 2022 LM-Steuerberatung | Alle Rechte vorbehalten</p>
</footer>
</body>
</html>
```